Business Card for Coastal Tundrabridge Advisory

We need a business card for Coastal Tundrabridge Advisory. The company website address is provided below. The company logo is attached. We provide specialized permafrost services to the mining, transportation, and oil & gas industries. The card should be prepared for:
Matthias Korhonen, PhD.
Coastal Tundrabridge Advisory
PO Box 418259
Quillwater, Alaska 99642
Direct: +1-907-555-0143
Email: mkorhonen@tundrabridgeadvisory.example
Website: www.coastaltundrabridgeadvisory.example

```html
<!DOCTYPE html>
<html lang="en">
<head>
<meta charset="utf-8">
<title>Coastal Tundrabridge Advisory – Business Card</title>
<link rel="stylesheet" href="https://fonts.googleapis.com/css2?family=Roboto:wght@300;400;500;700&display=swap">
<style>
  :root {
    --backdrop: #222222;
    --card: #111722;
    --ink: #ffffff;
    --ink-soft: #e4e7ec;
  }
  * { margin: 0; padding: 0; box-sizing: border-box; }
  html, body {
    width: 1200px; height: 711px; overflow: hidden;
    background: var(--backdrop);
    font-family: "Roboto", sans-serif;
    color: var(--ink);
  }
  .canvas {
    position: relative; width: 1200px; height: 711px;
    display: flex; align-items: center; justify-content: center; gap: 40px;
  }
  .card {
    position: relative; width: 540px; height: 309px;
    background: var(--card);
    box-shadow: 0 10px 28px rgba(0,0,0,.55);
  }
  /* Front */
  .brand {
    position: absolute; right: 44px; top: 92px;
    font-weight: 700; font-size: 30px; line-height: 1.08;
    letter-spacing: .5px; text-transform: uppercase; text-align: right;
    color: var(--ink);
  }
  .services {
    position: absolute; left: 0; right: 0; bottom: 34px; text-align: center;
  }
  .services-title { font-weight: 700; font-size: 11px; letter-spacing: .3px; margin-bottom: 3px; }
  .services-text { font-weight: 400; font-size: 10.5px; color: var(--ink-soft); }
  /* Back */
  .accent-bar {
    position: absolute; left: 22px; top: 26px; width: 9px; height: 48px;
    background: var(--ink);
  }
  .person { position: absolute; left: 38px; top: 24px; }
  .person-name { font-size: 24px; line-height: 1.05; }
  .person-name .first { font-weight: 700; }
  .person-name .last { font-weight: 300; }
  .person-title { font-size: 15px; font-weight: 500; margin-top: 2px; }
  .brand--small {
    top: 24px; right: 26px; font-size: 17px;
  }
  .contact {
    position: absolute; right: 24px; top: 150px;
    list-style: none; text-align: right;
    font-size: 12px; line-height: 1.75; color: var(--ink-soft);
  }
  .contact li { display: flex; justify-content: flex-end; align-items: center; gap: 6px; }
  .contact svg { width: 11px; height: 11px; fill: var(--ink); flex: none; }
  .address {
    position: absolute; left: 38px; bottom: 26px;
    font-size: 12.5px; line-height: 1.45; color: var(--ink-soft);
  }
</style>
</head>
<body>
<main class="canvas">
  <section class="card card--front">
    <div class="brand">Coastal<br>Tundrabridge Advisory</div>
    <div class="services">
      <p class="services-title">OUR SERVICES</p>
      <p class="services-text">We provide specialized permafrost services to the mining, transportation, and oil &amp; gas industries</p>
    </div>
  </section>

  <section class="card card--back">
    <span class="accent-bar"></span>
    <div class="person">
      <p class="person-name"><span class="first">Matthias</span> <span class="last">Korhonen</span></p>
      <p class="person-title">PhD</p>
    </div>
    <div class="brand brand--small">Coastal<br>Tundrabridge Advisory</div>

    <ul class="contact">
      <li>+1-907-555-0143
        <svg viewBox="0 0 24 24" aria-hidden="true"><path d="M6.6 10.8a15 15 0 0 0 6.6 6.6l2.2-2.2a1 1 0 0 1 1-.25 11.4 11.4 0 0 0 3.6.57 1 1 0 0 1 1 1V20a1 1 0 0 1-1 1A17 17 0 0 1 3 4a1 1 0 0 1 1-1h3.5a1 1 0 0 1 1 1c0 1.25.2 2.45.57 3.57a1 1 0 0 1-.25 1z"/></svg></li>
      <li>mkorhonen@tundrabridgeadvisory.example
        <svg viewBox="0 0 24 24" aria-hidden="true"><path d="M2 5h20v14H2z M4 7v.5l8 5 8-5V7l-8 5z" fill-rule="evenodd"/></svg></li>
      <li>www.coastaltundrabridgeadvisory.example
        <svg viewBox="0 0 24 24" aria-hidden="true"><circle cx="12" cy="12" r="10"/></svg></li>
    </ul>

    <div class="address">
      <p>PO Box 418259</p>
      <p>Quillwater, Alaska 99642</p>
    </div>
  </section>
</main>
</body>
</html>
```